Lotus Market Hall VIP Card(Magnetic strip plastic card)

We need Fancy,Simple,VIP customer card design for a grocery store name"Lotus Market Hall", Chinese name"福润商场“.Major color should be Dark red. This design is based on a VIP gift card project, which means design should consider about the back side with magnetic strip area and mostly it will be plastic material.

Target Market(s)

Rich Customers

Industry/Entity Type

Grocery Store

Contact Information for Business Card

People actually put more than $1000 into the card for shopping

Font styles to use
Serif
Sans Serif
Decorative
Script
Other font styles liked:
• Fancy

Colors
ec1f27
fbed22

Requirements
Must have
• Red color
Nice to have
• Better logo transformation.

```html
<!DOCTYPE html>
<html lang="en">
<head>
<meta charset="utf-8">
<title>Lotus Market Hall VIP Card</title>
<link href="https://fonts.googleapis.com/css2?family=Arimo:wght@400;700&family=Tinos:wght@700&family=Noto+Sans+SC:wght@700&display=swap" rel="stylesheet">
<style>
  :root {
    --card-red: #ec1f27;
    --card-yellow: #f5ec22;
    --strip-black: #000000;
    --fine-print: #9a9136;
    --page-bg: #ffffff;
  }
  html, body { margin: 0; padding: 0; overflow: hidden; }
  body {
    width: 1200px; height: 1200px; position: relative;
    background: var(--page-bg);
    font-family: "Arimo", "Noto Sans SC", sans-serif;
  }
  .card {
    position: absolute; overflow: hidden; border-radius: 14px;
    background: var(--card-yellow);
  }
  .card--shadow { box-shadow: 0 22px 40px rgba(0,0,0,0.28); }
  .card__red { position: absolute; left: 0; right: 0; top: 0; background: var(--card-red); }
  .strip { position: absolute; left: 0; right: 0; background: var(--strip-black); }
  .brand {
    position: absolute; color: var(--card-yellow); font-weight: 700;
    text-align: center; line-height: 1.05; white-space: nowrap;
  }
  .brand__cn { display: block; }
  .brand__en { display: block; }
  .dot { position: absolute; border-radius: 50%; background: var(--card-yellow); }
  .vip {
    position: absolute; margin: 0; color: var(--card-yellow);
    font-family: "Tinos", "Times New Roman", serif; font-weight: 700; line-height: 1;
  }
  .tagline {
    position: absolute; left: 0; right: 0; margin: 0; text-align: center;
    color: var(--card-red); white-space: nowrap;
  }
  .holder {
    position: absolute; margin: 0; color: var(--card-yellow);
    letter-spacing: 1.5px; line-height: 1; white-space: nowrap;
  }
  .terms {
    position: absolute; margin: 0; color: var(--fine-print);
    text-align: justify; text-align-last: left;
  }

  /* top pair */
  .back-lg { left: 512px; top: 346px; width: 585px; height: 367px; }
  .back-lg .card__red { height: 252px; }
  .back-lg .strip { top: 45px; height: 60px; }
  .back-lg .dot { left: 162px; top: 172px; width: 28px; height: 28px; }
  .back-lg .holder { left: 206px; top: 170px; font-size: 32px; }
  .back-lg .terms { left: 22px; width: 548px; top: 260px; font-size: 13px; line-height: 16px; }

  .front-lg { left: 94px; top: 115px; width: 584px; height: 367px; }
  .front-lg .card__red { height: 252px; }
  .front-lg .brand { left: 118px; top: 102px; width: 140px; }
  .front-lg .brand__cn { font-size: 30px; }
  .front-lg .brand__en { font-size: 13px; margin-top: 6px; }
  .front-lg .dot { left: 261px; top: 131px; width: 32px; height: 32px; }
  .front-lg .vip { left: 302px; top: 104px; font-size: 104px; }
  .front-lg .tagline { top: 285px; font-size: 18px; }

  /* bottom pair */
  .front-sm { left: 94px; top: 829px; width: 468px; height: 294px; }
  .front-sm .card__red { height: 202px; }
  .front-sm .brand { left: 96px; top: 90px; width: 110px; }
  .front-sm .brand__cn { font-size: 24px; }
  .front-sm .brand__en { font-size: 10.5px; margin-top: 5px; }
  .front-sm .dot { left: 209px; top: 104px; width: 26px; height: 26px; }
  .front-sm .vip { left: 242px; top: 81px; font-size: 82px; }
  .front-sm .tagline { top: 228px; font-size: 15px; }

  .back-sm { left: 628px; top: 829px; width: 469px; height: 294px; }
  .back-sm .card__red { height: 202px; }
  .back-sm .strip { top: 36px; height: 49px; }
  .back-sm .dot { left: 130px; top: 139px; width: 22px; height: 22px; }
  .back-sm .holder { left: 165px; top: 137px; font-size: 26px; letter-spacing: 1.2px; }
  .back-sm .terms { left: 17px; width: 440px; top: 209px; font-size: 10.4px; line-height: 13px; }
</style>
</head>
<body>

  <section class="card card--shadow back-lg" aria-label="VIP card back">
    <div class="card__red"></div>
    <div class="strip"></div>
    <span class="dot"></span>
    <p class="holder">LEO MARSH</p>
    <p class="terms">This "Card" contains value which may be used to purchase goods with the exception of other Cards. Please present it to a sales associate at the time of purchase and amounts will be deducted from the Card balance. This Card may not be redeemed for cash and the unused value remains on the Card. Merchant is not responsible for lost, stolen or damaged Cards or any unauthorized use.</p>
  </section>

  <section class="card card--shadow front-lg" aria-label="VIP card front">
    <div class="card__red"></div>
    <div class="brand"><span class="brand__cn">福润商场</span><span class="brand__en">Lotus Market Hall</span></div>
    <span class="dot"></span>
    <p class="vip">VIP</p>
    <p class="tagline">People actually put more than $1000 into the card for shopping</p>
  </section>

  <section class="card front-sm" aria-label="VIP card front, flat view">
    <div class="card__red"></div>
    <div class="brand"><span class="brand__cn">福润商场</span><span class="brand__en">Lotus Market Hall</span></div>
    <span class="dot"></span>
    <p class="vip">VIP</p>
    <p class="tagline">People actually put more than $1000 into the card for shopping</p>
  </section>

  <section class="card back-sm" aria-label="VIP card back, flat view">
    <div class="card__red"></div>
    <div class="strip"></div>
    <span class="dot"></span>
    <p class="holder">LEO MARSH</p>
    <p class="terms">This "Card" contains value which may be used to purchase goods with the exception of other Cards. Please present it to a sales associate at the time of purchase and amounts will be deducted from the Card balance. This Card may not be redeemed for cash and the unused value remains on the Card. Merchant is not responsible for lost, stolen or damaged Cards or any unauthorized use.</p>
  </section>

</body>
</html>
```